Animal Eye Clinic needs a Business card

We are a new veterinary ophthalmology practice (Ridgeline Pet Vision Care) and we need a business card designed. We only see animal eyes - we are not a regular veterinary clinic. We already have a logo. We are looking for a professional, good looking business card to hand out to our clients. We are looking for something simple but professional and contemporary. Our logo is likely the only picture/graphic that needs to be on the card.
Updates

Contact Information for Business Card

Delia Vossman, BSc, DVM, MSc, DipACVO
Veterinary Ophthalmologist

Phone: 250.418.3927
Email: ridgelinepetvisioncare@mailbox-example.net
Website: ridgelinepetvisioncare-example.net
Address: 1874 Thornbury Rd
Kelowna, BC, V1X 4M9

Colors

Designer to choose colors to be used in the design.

Requirements
Must have
• Our logo (attached)

```html
<!DOCTYPE html>
<html lang="en">
<head>
<meta charset="utf-8">
<title>Ridgeline Pet Vision Care – Business Card</title>
<link rel="stylesheet" href="https://fonts.googleapis.com/css2?family=Archivo:wght@700;800&family=Roboto+Condensed:ital,wght@0,400;0,700;1,700&display=swap">
<style>
  :root {
    --teal: #1b99a9;
    --teal-dark: #17889a;
    --teal-text: #1a97a8;
    --ink: #5a5a5a;
    --paper: #ffffff;
    --backdrop: #262626;
  }
  * { margin: 0; padding: 0; box-sizing: border-box; }
  html, body { width: 1200px; height: 900px; overflow: hidden; }
  body {
    background: var(--backdrop);
    font-family: "Roboto Condensed", sans-serif;
    display: flex;
    flex-direction: column;
    align-items: center;
    justify-content: center;
    gap: 40px;
  }
  .card {
    width: 700px;
    height: 400px;
    position: relative;
    overflow: hidden;
  }

  /* Reverse side */
  .card-back { background: var(--teal); }
  .card-back .pattern {
    position: absolute; inset: 0;
    background: linear-gradient(135deg, var(--teal) 0%, var(--teal-dark) 100%);
  }
  .card-back .brand {
    position: absolute; inset: 0;
    display: flex; align-items: center; justify-content: center; gap: 14px;
  }
  .brand-dot {
    width: 22px; height: 22px; border-radius: 50%;
    background: var(--paper);
  }
  .brand-name {
    color: var(--paper);
    font-family: "Roboto Condensed", sans-serif;
    font-weight: 700;
    font-size: 30px;
    text-transform: uppercase;
    letter-spacing: 1px;
  }

  /* Front side */
  .card-front { background: var(--paper); }
  .card-front .band {
    height: 125px;
    background: var(--teal);
    display: flex; align-items: center; gap: 14px;
    padding-left: 48px;
  }
  .card-front .band .brand-name { font-size: 26px; }
  .person { padding: 26px 0 0 48px; }
  .person-name {
    font-family: "Archivo", sans-serif;
    font-weight: 800;
    font-size: 38px;
    color: var(--teal-text);
    text-transform: uppercase;
    line-height: 1;
    letter-spacing: 0.5px;
  }
  .person-credentials {
    font-weight: 700; font-style: italic;
    font-size: 19px;
    color: var(--teal-text);
    margin-top: 4px;
  }
  .person-title {
    font-size: 21px;
    color: var(--ink);
    margin-top: 1px;
  }
  .contact {
    list-style: none;
    position: absolute; left: 48px; top: 268px;
  }
  .contact li {
    display: flex; align-items: center; gap: 10px;
    font-size: 20px; color: var(--ink);
    line-height: 30px;
  }
  .contact svg { width: 20px; height: 20px; flex: none; }
  .address {
    position: absolute; right: 40px; bottom: 26px;
    text-align: right;
    font-size: 21px; color: var(--ink);
    line-height: 26px;
  }
</style>
</head>
<body>

  <section class="card card-back">
    <div class="pattern" role="img" aria-label="Faint repeating pattern of the clinic emblem in deeper teal"></div>
    <div class="brand">
      <span class="brand-dot"></span>
      <span class="brand-name">Ridgeline Pet Vision Care</span>
    </div>
  </section>

  <section class="card card-front">
    <header class="band">
      <span class="brand-dot"></span>
      <span class="brand-name">Ridgeline Pet Vision Care</span>
    </header>

    <div class="person">
      <h1 class="person-name">Delia Vossman</h1>
      <p class="person-credentials">BSc, DVM, MSc, DipACVO</p>
      <p class="person-title">Veterinary Ophthalmologist</p>
    </div>

    <ul class="contact">
      <li>
        <svg viewBox="0 0 24 24" fill="none" stroke="var(--teal-text)" stroke-width="1.8"><circle cx="12" cy="12" r="10"/><path d="M8.5 7.5c-.8.8-.6 2.6 1.4 4.8s4 2.6 4.9 1.7l.8-.8-2-1.6-1 .8c-.7-.2-2.1-1.6-2.3-2.3l.8-1-1.6-2z" fill="var(--teal-text)" stroke="none"/></svg>
        <span>250.418.3927</span>
      </li>
      <li>
        <svg viewBox="0 0 24 24" fill="none" stroke="var(--teal-text)" stroke-width="1.8"><rect x="2" y="5" width="20" height="14" rx="1"/><path d="M2 5l10 8 10-8"/></svg>
        <span>ridgelinepetvisioncare@mailbox-example.net</span>
      </li>
      <li>
        <svg viewBox="0 0 24 24" fill="none" stroke="var(--teal-text)" stroke-width="1.8"><circle cx="12" cy="12" r="10"/><path d="M2 12h20M12 2c3 3 3 17 0 20M12 2c-3 3-3 17 0 20"/></svg>
        <span>www.ridgelinepetvisioncare-example.net</span>
      </li>
    </ul>

    <address class="address" style="font-style:normal">
      1874 Thornbury Rd<br>
      Kelowna, BC, V1X 4M9
    </address>
  </section>

</body>
</html>
```